Brindlewick Cellars Winery… For non-interventionist winemakers, wine-making begins in the

Need a new website for my new winery…previous one lost in divorce to my cheating ex wife…sigh. Calling it Brindlewick Cellars. Want it to look like a wedding sight…calligraphy writing…black and white…with some black roses…want the look of a invitational wedding site…celebratory! We employ a combination of modern techniques and old world traditions, practicing both the cuvee and "field blending" methods, to create a range of distinctive varietals. To ensure flawless berries reach the fermentation process, we hand-sort grapes as soon as we get them into the winery. Our open-top, double-jacketed fermenters allow precise temperature control during "cold soak" periods and primary fermentation -- essential for color, flavor, and tannin extraction. Occasional délestage ("rack & return") aerates the wine. After ratchet basket pressing, we age our wines in French oak barrels for at least 18 months; minimal racking lets wine clarify naturally. Patience, sagacity, gumption, and a balance between both received methods (classic and modern) and ingenuity are foundations for crafting the world-class wines offered by our small, family-run artisanal winery here in the beautiful Walla Walla valley, located beneath the Blue Mountains in eastern Washington

Target Market(s)

Wine drinkers/broken hearts

Industry/Entity Type

Winery

Number of Pages Required

4 page

Font styles to use
Script

Colors

Designer to choose only greyscale colors for use in the design.

Requirements
Must have
• Black roses… From our Walla Walla valley boutique winery here in the Pacific Northwest, we offer a range of premium reds, whites, ice wines, late harvest wines, brandies, grappas, and specialty spirits. We embrace sustainable farming methods on our estate vineyard and source fruit from growers who share our commitment to biodiversity. A great bottle of wine begins with the vine! For our "green wines," we practice innovative eco-friendly techniques, aim for Earth-friendly packaging, and donate a portion of our after-profit proceeds to environmental concerns. Though we appreciate ratings, we're less interested in numbers and more in the approval of our palettes and those of trusted friends, as well as accolades from loyal customers near and far. We handcraft what we hope will become your cult wines, often well into the night, humbled by the calls of barn owls who give our cellar its name.
Nice to have
• Page to list varieties…Tamarack Tokaji, Lanternfall Lambrusco, Cobblemoor Claret

```html
<!DOCTYPE html>
<html lang="en">
<head>
<meta charset="utf-8">
<title>Brindlewick Cellars Winery</title>
<link href="https://fonts.googleapis.com/css2?family=Pinyon+Script&family=Roboto:wght@400;500;700&display=swap" rel="stylesheet">
<style>
:root{
  --cream:#f5f4ec;
  --ink:#333333;
  --text:#666666;
  --dark:#222222;
  --darker:#111111;
  --button:#3b3b3b;
  --white:#ffffff;
}
*{box-sizing:border-box;margin:0;padding:0}
html,body{width:1200px;height:4580px;overflow:hidden}
body{background:var(--cream);font-family:"Roboto",sans-serif;color:var(--text);position:relative}
.abs{position:absolute}
.script{font-family:"Pinyon Script",cursive;color:var(--ink);font-weight:400}
.logo{font-family:"Pinyon Script",cursive;color:var(--ink);text-align:center;line-height:.9;width:400px;left:400px;z-index:2}
.logo span{display:block}
.logo .l1{font-size:62px}
.logo .l2{font-size:42px}
.nav{display:flex;justify-content:center;left:0;width:1200px;font-size:13px;font-weight:500;letter-spacing:.5px;color:var(--ink);text-transform:uppercase;z-index:2}
.roses{background:radial-gradient(circle at 40% 40%,#5d6262,#2f3333 70%,transparent 72%);z-index:1}
.btn{display:inline-block;background:var(--button);color:var(--white);font-weight:500;font-size:15px;border-radius:22px;text-align:center}
.hero{left:0;top:205px;width:1200px;height:652px;background:linear-gradient(100deg,#c9ccca 0%,#9a9e9c 45%,#4a4f4d 75%,#2e3231 100%)}
.hero-card{left:112px;top:359px;width:514px;height:336px;background:var(--white);border-radius:22px;padding:26px 44px;z-index:2}
.hero-card h1{font-size:52px;line-height:68px}
.hero-card p{font-size:13.5px;line-height:27px;margin:16px 0 20px}
.hero-card .btn{width:134px;height:42px;line-height:42px}
.about{left:0;top:857px;width:1200px;height:1060px;background:linear-gradient(180deg,#efefe7 0%,#e2e2dc 50%,#cfd0cc 65%)}
.about-land{left:0;top:690px;width:1200px;height:370px;background:linear-gradient(180deg,#c5c6c2,#7a7d7b 45%,#3c3f3e)}
.about-card{left:251px;top:992px;width:698px;height:594px;background:var(--white);border-radius:14px;overflow:hidden;z-index:1}
.about-text{left:251px;top:992px;width:698px;text-align:center;padding:92px 60px 0;z-index:3}
.about-text h2{font-size:44px;margin-bottom:14px}
.about-text p{font-size:13.5px;line-height:28.4px}
.section-title{font-size:44px;text-align:center;left:0;width:1200px;z-index:2}
.products-intro{left:170px;width:860px;text-align:center;font-size:14.5px;line-height:30px;z-index:2}
.product{width:306px;height:391px;background:#f9f8f3;border-radius:14px;box-shadow:0 4px 16px rgba(0,0,0,.08);text-align:center;top:2231px;z-index:2}
.product .photo{margin:2px 4px 0;height:210px;border-radius:12px}
.product h3{font-size:16.5px;font-weight:500;color:var(--ink);margin:26px 0 10px}
.product p{font-size:13px;line-height:26px;padding:0 22px}
.product .btn{position:absolute;left:86px;bottom:-20px;width:134px;height:42px;line-height:42px}
.why-text{left:585px;top:2860px;width:510px;z-index:3}
.why-text h2{font-size:44px;margin-bottom:12px}
.why-text p{font-size:13.8px;line-height:31px;margin-bottom:31px}
.why-text .btn{width:134px;height:42px;line-height:42px}
.contact{left:0;top:3543px;width:1200px;height:697px;background:var(--dark)}
.contact-box{left:169px;top:3657px;width:862px;height:469px;background:var(--darker);border-radius:22px}
.contact-box h2{color:var(--white);font-size:44px;text-align:center;margin-top:66px}
.field{border:1px solid #8a8a8a;color:var(--white);font-size:12px;padding:14px 28px}
.submit{background:var(--white);color:var(--darker);font-size:14px;font-weight:700;text-align:center;line-height:57px}
.social{top:4475px;width:39px;height:39px;border-radius:50%;background:var(--dark);z-index:2}
.copy{left:0;width:1200px;text-align:center;font-size:11px;top:4537px;color:var(--ink);z-index:2}
</style>
</head>
<body>

<!-- Header -->
<div class="abs roses" role="img" aria-label="Black roses and leaves" style="left:-40px;top:-40px;width:230px;height:220px"></div>
<div class="abs logo" style="top:28px"><span class="l1">Brindlewick</span><span class="l2">Cellars</span></div>
<nav class="abs nav" style="top:154px">
  <span style="margin-right:80px">Home</span><span style="margin-right:80px">Wine</span><span>Contact Us</span>
</nav>

<!-- Hero -->
<div class="abs hero" role="img" aria-label="Black and white photo of grape clusters in a vineyard"></div>
<div class="abs hero-card">
  <h1 class="script">Welcome To<br>Brindlewick Cellars</h1>
  <p>Lorem ipsum dolor sit amet, consectetur adipiscing elit, sed do eiusmod tempor incididunt ut labore et dolore magna aliqua. Quis ipsum suspendisse ultrices gravida.</p>
  <span class="btn">Get Started</span>
</div>

<!-- About -->
<div class="abs about"><div class="abs about-land" role="img" aria-label="Vineyard valley landscape with wine bottle and glass"></div></div>
<div class="abs about-card">
  <div class="abs roses" role="img" aria-label="Black roses" style="right:-40px;top:-40px;width:170px;height:140px"></div>
  <div class="abs roses" role="img" aria-label="Black roses" style="left:-30px;bottom:-40px;width:170px;height:130px"></div>
</div>
<div class="abs about-text">
  <h2 class="script">About Us</h2>
  <p>We employ a combination of modern techniques and old world traditions, practicing both the cuvee and "field blending" methods, to create a range of distinctive varietals. To ensure flawless berries reach the fermentation process, we hand-sort grapes as soon as we get them into the winery. Our open-top, double-jacketed fermenters allow precise temperature control during "cold soak" periods and primary fermentation – essential for color, flavor, and tannin extraction. Occasional délestage ("rack &amp; return") aerates the wine. After ratchet basket pressing, we age our wines in French oak barrels for at least 18 months; minimal racking lets wine clarify naturally. Patience, sagacity, gumption, and a balance between both received methods (classic and modern) and ingenuity are foundations for crafting the world-class wines offered by our small, family-run artisanal winery here in the beautiful Walla Walla valley, located beneath the Blue Mountains in eastern Washington</p>
</div>

<!-- Products -->
<div class="abs roses" role="img" aria-label="Black roses and leaves" style="left:-60px;top:1910px;width:300px;height:180px"></div>
<h2 class="abs script section-title" style="top:2036px">Our Wine Products</h2>
<p class="abs products-intro" style="top:2106px">At vero eos et accusamus et iusto odio dignissimos ducimus qui blanditiis praesentium voluptatum deleniti atque corrupti quos dolores et quas molestias excepturi sint occaecati cupiditate non provident, similique sunt in culpa qui officia</p>

<div class="abs product" style="left:112px">
  <div class="photo" role="img" aria-label="Wine bottles stacked in a wooden rack" style="background:linear-gradient(135deg,#8a8a88,#2c2c2c)"></div>
  <h3>Tamarack Tokaji</h3>
  <p>Lorem ipsum dolor sit amet, consecte tur adipiscing elit, sed do eiusmod tempor incididunt ut labore et dolore</p>
  <span class="btn">Buy Now</span>
</div>
<div class="abs product" style="left:446px">
  <div class="photo" role="img" aria-label="Wine being poured into a glass" style="background:linear-gradient(135deg,#3a3a3a,#9a9a9a 60%,#4a4a4a)"></div>
  <h3>Lanternfall Lambrusco</h3>
  <p>Lorem ipsum dolor sit amet, consecte tur adipiscing elit, sed do eiusmod tempor incididunt ut labore et dolore</p>
  <span class="btn">Buy Now</span>
</div>
<div class="abs product" style="left:782px">
  <div class="photo" role="img" aria-label="Wine bottle and glasses beside an oak barrel" style="background:linear-gradient(135deg,#6a6a6a,#c4c4c4 55%,#555)"></div>
  <h3>Cobblemoor Claret</h3>
  <p>Lorem ipsum dolor sit amet, consecte tur adipiscing elit, sed do eiusmod tempor incididunt ut labore et dolore</p>
  <span class="btn">Buy Now</span>
</div>

<!-- Why choose us -->
<div class="abs" role="img" aria-label="Red wine bottle with two glasses, grapes, corkscrew and cork" style="left:133px;top:2800px;width:409px;height:622px;background:radial-gradient(ellipse at 40% 55%,#3a2a2c 0%,#5a4a4c 35%,rgba(245,244,236,0) 70%)"></div>
<div class="abs why-text">
  <h2 class="script">Why Choose Us</h2>
  <p>Black roses... From our Walla Walla valley boutique winery here in the Pacific Northwest, we offer a range of premium reds, whites, ice wines, late harvest wines, brandies, grappas, and specialty spirits. We embrace sustainable farming methods on our estate vineyard and source fruit from growers who share our commitment to biodiversity.</p>
  <p>A great bottle of wine begins with the vine! For our "green wines," we practice innovative eco-friendly techniques, aim for Earth-friendly packaging, and donate a portion of our after-profit proceeds to environmental concerns. Though we appreciate ratings, we're less interested in numbers and more in the approval of our palettes and those of trusted friends, as well as accolades from loyal customers near and</p>
  <span class="btn">Read More</span>
</div>
<div class="abs roses" role="img" aria-label="Black roses" style="left:1000px;top:3360px;width:260px;height:230px"></div>

<!-- Contact -->
<div class="abs contact" role="img" aria-label="Dark background of grape clusters"></div>
<div class="abs contact-box"><h2 class="script">Get In Touch With Us</h2></div>
<div class="abs field" style="left:247px;top:3833px;width:336px;height:56px">Full Name</div>
<div class="abs field" style="left:247px;top:3910px;width:336px;height:56px">Email Address</div>
<div class="abs field" style="left:247px;top:3986px;width:336px;height:57px">Contact Number</div>
<div class="abs field" style="left:615px;top:3833px;width:338px;height:133px">Comments</div>
<div class="abs submit" style="left:615px;top:3986px;width:338px;height:57px">Submit Here</div>

<!-- Footer -->
<div class="abs roses" role="img" aria-label="Black roses" style="left:-60px;top:4400px;width:220px;height:220px"></div>
<div class="abs roses" role="img" aria-label="Black roses" style="left:1040px;top:4400px;width:220px;height:220px"></div>
<div class="abs logo" style="top:4300px"><span class="l1">Brindlewick</span><span class="l2">Cellars</span></div>
<nav class="abs nav" style="top:4429px">
  <span style="margin-right:70px">Home</span><span style="margin-right:70px">Wine</span><span style="margin-right:70px">About Us</span><span style="margin-right:70px">Why Choose Us?</span><span>Contact Us</span>
</nav>
<span class="abs social" style="left:535px"></span>
<span class="abs social" style="left:581px"></span>
<span class="abs social" style="left:626px"></span>
<p class="abs copy">(C) Copyright 2024 | All Rights Reserved</p>

</body>
</html>
```